RK Donnelly & Associates

Create a website encompassing design work already carried out for business card.
Small accounting practice, business accounting and management, superannuation, audit, taxation.

```html
<!DOCTYPE html>
<html lang="en">
<head>
<meta charset="utf-8">
<title>RK Donnelly &amp; Associates</title>
<link href="https://fonts.googleapis.com/css2?family=Open+Sans:wght@400;600&display=swap" rel="stylesheet">
<style>
:root{
  --page:#ececec;
  --dark:#262626;
  --blue:#6aa6dc;
  --band:#6fa9de;
  --panel:#f5f5f5;
  --line:#dcdcdc;
  --text:#8a8a8a;
  --heading:#555;
  --ink:#333;
  --white:#fff;
}
*{box-sizing:border-box;margin:0;padding:0}
html,body{width:1104px;height:1200px;overflow:hidden}
body{background:var(--page);font-family:"Open Sans",Arial,sans-serif;position:relative}
.site{position:absolute;left:91px;top:0;width:922px;height:1106px;background:var(--white)}
.header{position:absolute;left:0;top:0;width:922px;height:100px;background:var(--dark)}
.brand{position:absolute;left:76px;top:26px;display:flex;align-items:center;gap:12px}
.brand-mark{width:40px;height:40px;background:var(--blue)}
.brand-name{color:var(--white);font-size:19px;font-weight:600;line-height:21px;width:160px}
.nav{position:absolute;right:10px;top:58px;display:flex;gap:32px;list-style:none}
.nav li{color:var(--white);font-size:13px}
.nav li.current{color:var(--blue)}
.tagline{position:absolute;left:0;top:100px;width:922px;height:23px;background:var(--band);color:var(--white);font-size:8px;font-weight:600;line-height:23px;padding-left:11px}
.hero{position:absolute;left:0;top:123px;width:922px;height:417px}
.hero-photo{position:absolute;inset:0;background:linear-gradient(90deg,#d9dde2 0%,#e9ecef 20%,#f2f4f6 60%,#fbfcfd 100%)}
.hero-title{position:absolute;right:48px;top:112px;text-align:right;color:#4f4f4f;font-size:31px;line-height:37px}
.hero-btn{position:absolute;left:779px;top:193px;width:93px;height:36px;background:#474747;color:var(--white);font-size:13px;line-height:36px;text-align:center}
.hero-arrows{position:absolute;left:830px;top:249px;width:42px;height:38px}
.welcome{position:absolute;left:0;top:574px;width:922px;text-align:center}
.welcome h1{color:var(--blue);font-size:23px;font-weight:400;line-height:30px}
.welcome p{margin:8px auto 0;width:830px;color:var(--text);font-size:12.5px;line-height:21px}
.services{position:absolute;left:10px;top:701px;width:901px;height:291px;border:1px solid var(--line);background:var(--panel)}
.service-list{position:absolute;left:0;top:0;width:209px;height:289px;list-style:none;border-right:1px solid var(--line)}
.service-list li{height:58px;border-bottom:1px solid var(--line);background:var(--white);display:flex;align-items:center;padding-left:15px;gap:14px;font-size:14.5px;color:var(--ink)}
.service-list li:last-child{border-bottom:none}
.service-list li.active{background:var(--panel)}
.service-list svg{width:18px;height:18px;fill:#666}
.service-detail{position:absolute;left:240px;top:12px;width:640px}
.service-detail h2{color:var(--blue);font-size:22px;font-weight:400;line-height:30px}
.service-detail p{color:var(--text);font-size:12.5px;line-height:21px}
.service-intro{margin-top:12px}
.service-media{position:absolute;left:3px;top:149px;width:205px;height:103px;background:linear-gradient(180deg,#d5dde6 0%,#7e8a96 55%,#2c323a 100%);border:2px solid var(--white)}
.service-more{position:absolute;left:232px;top:142px;width:432px}
.contact{position:absolute;left:0;top:1026px;width:922px;height:60px}
.contact-item{position:absolute;top:0;display:flex;align-items:center;gap:10px;color:var(--text);font-size:12.5px;line-height:21px;height:42px}
.contact-item svg{width:26px;height:26px;fill:#999}
.footer{position:absolute;left:0;top:1106px;width:1104px;height:94px;background:var(--dark)}
.footer-links{position:absolute;left:93px;top:18px;color:#cfcfcf;font-size:12.5px;list-style:none;display:flex}
.footer-links li+li::before{content:"|";margin:0 13px}
.copyright{position:absolute;left:93px;top:54px;color:#cfcfcf;font-size:12px}
.social{position:absolute;left:892px;top:34px;display:flex;gap:8px}
.social span{width:24px;height:24px;border-radius:50%;background:#5a5a5a;display:block}
.social svg{width:24px;height:24px}
</style>
</head>
<body>
<div class="site">
  <header class="header">
    <div class="brand"><span class="brand-mark"></span><span class="brand-name">RK Donnelly &amp; Associates</span></div>
    <ul class="nav">
      <li class="current">HOME</li><li>ABOUT US</li><li>SERVICES</li><li>CONTACT US</li>
    </ul>
  </header>
  <div class="tagline">Accountant · Business Solutions · Management · Superannuation · Audit</div>

  <section class="hero">
    <div class="hero-photo" role="img" aria-label="Photo of a smiling accountant in a dark suit at a bright office desk with a calculator and binder"></div>
    <h2 class="hero-title" style="font-weight:400">Morbi varius aliquam<br>risus at efficitur</h2>
    <div class="hero-btn">Read more</div>
    <svg class="hero-arrows" viewBox="0 0 42 38" aria-hidden="true">
      <ellipse cx="21" cy="19" rx="21" ry="19" fill="#3d3d3d"/>
      <line x1="21" y1="2" x2="21" y2="36" stroke="#666" stroke-width="1"/>
      <path d="M15 14l-5 5 5 5M27 14l5 5-5 5" fill="none" stroke="#fff" stroke-width="2.5"/>
    </svg>
  </section>

  <section class="welcome">
    <h1>Welcome to RK Donnelly &amp; Associates</h1>
    <p>Integer sit amet rhoncus lorem. Cras vel mi mi. Fusce justo mauris, varius ac ullamcorper suscipit, convallis vitae erat. Phasellus faucibus fringilla libero, in suscipit dolor ultrices non. Sed euismod ex et sem consectetur, sit amet vulputate turpis dictum. Vestibulum id felis dictum, scelerisque massa sit amet, scelerisque lorem. Donec faucibus velit eu dictum euismod. Sed dictum pulvinar mi, in rhoncus dui.</p>
  </section>

  <section class="services">
    <ul class="service-list">
      <li class="active"><svg viewBox="0 0 18 18"><rect x="4" y="1" width="10" height="16" rx="1"/><rect x="6" y="3" width="6" height="3" fill="#fff"/></svg>Accounting</li>
      <li><svg viewBox="0 0 18 18"><path d="M3 6h4a2 2 0 1 1 4 0h4v4a2 2 0 1 1 0 4v3H3z"/></svg>Business&nbsp; Solutions</li>
      <li><svg viewBox="0 0 18 18"><circle cx="5" cy="7" r="2.5"/><circle cx="13" cy="7" r="2.5"/><circle cx="9" cy="5" r="3"/><path d="M1 15c0-4 8-4 8-4s8 0 8 4z"/></svg>Mangement</li>
      <li><svg viewBox="0 0 18 18"><ellipse cx="9" cy="10" rx="8" ry="6"/></svg>Superaanuation</li>
      <li><svg viewBox="0 0 18 18"><path d="M2 4h8v2H4v9h9V9h2v8H2z"/><path d="M8 11l1-3 7-7 2 2-7 7z"/></svg>Audit</li>
    </ul>
    <div class="service-detail">
      <h2>Accounting</h2>
      <p class="service-intro">Aenean arcu metus, porta vitae elementum eu, tempus vitae dolor. Aenean in purus et augue tempus molestie quis vitae felis. Aenean blandit viverra libero malesuada lacinia. Lorem ipsum dolor sit amet, consectetur adipiscing elit. Pellentesque mattis maximus dolor vitae semper. Morbi scelerisque nibh dui, vel fermentum dui viverra sed. Cras fermentum luctus mi eu dignissim.</p>
      <div class="service-media" role="img" aria-label="Photo of business people in silhouette talking in a bright meeting room"></div>
      <p class="service-more">Aliquam aliquet orci dolor, eget laoreet ipsum feugiat ac. Vivamus volutpat sem id metus commodo, a posuere nisi gravida. Donec at nunc dolor. Nulla rhoncus blandit cursus. Fusce laoreet auctor felis, eu efficitur libero ornare eget. Etiam pellentesque tortor in nulla tincidunt, id aliquet neque viverra. Pellentesque vel pharetra massa.</p>
    </div>
  </section>

  <section class="contact">
    <div class="contact-item" style="left:24px"><svg viewBox="0 0 26 26"><path d="M3 2h20v22H3zM6 5v16h14V5z"/><path d="M9 8h8v8l-4-3-4 3z"/></svg><span>55, Building name, streetname<br>City - Zip code</span></div>
    <div class="contact-item" style="left:282px"><svg viewBox="0 0 26 26"><path d="M4 5l5-3 4 6-3 2c1 3 3 5 6 7l2-3 6 4-3 5C12 22 5 15 4 5z"/></svg><span>Phone: 555 010 2468</span></div>
    <div class="contact-item" style="left:506px"><svg viewBox="0 0 26 26"><path d="M8 2h10v6H8zM3 9h20v15H3z"/><rect x="12" y="12" width="8" height="9" fill="#fff"/></svg><span>Fax : 555 010 1357</span></div>
    <div class="contact-item" style="left:706px"><svg viewBox="0 0 26 26"><path d="M1 6h24v15H1z"/><path d="M1 6l12 9 12-9" fill="none" stroke="#fff" stroke-width="1.5"/></svg><span>E-mail : info@rkdonnelly.com</span></div>
  </section>
</div>

<footer class="footer">
  <ul class="footer-links"><li>Home</li><li>About us</li><li>Services</li><li>Contact us</li></ul>
  <p class="copyright">Copyright &copy; 2014 &nbsp;RK Donnelly &amp; Associates. &nbsp;All rights reserved.</p>
  <div class="social">
    <span aria-label="Social profile"></span>
    <span aria-label="Social profile"></span>
    <span aria-label="Social profile"></span>
    <svg viewBox="0 0 24 24" aria-label="Email"><circle cx="12" cy="12" r="12" fill="#5a5a5a"/><rect x="6" y="8" width="12" height="8" fill="none" stroke="#ccc" stroke-width="1.3"/><path d="M6 8l6 5 6-5" fill="none" stroke="#ccc" stroke-width="1.3"/></svg>
  </div>
</footer>
</body>
</html>
```